Redesign of business card for Cedar Ridge Mechanical

We are looking for a new design for our business cards for Cedar Ridge Mechanical. We are a plumbing & HVAC construction company, operating on the West Coast of Canada and USA. Logo attached.
Industry/Entity Type
Construction - Plumbing & HVAC
Contact Information for Business Card
Name, address, phone numbers, email, website address
Look and feel
Each slider illustrates characteristics of the customer's brand and the style your logo design should communicate.

```html
<!DOCTYPE html>
<html lang="en">
<head>
<meta charset="utf-8">
<title>Cedar Ridge Mechanical – Business Cards</title>
<link rel="stylesheet" href="https://fonts.googleapis.com/css2?family=Open+Sans:wght@400;700&display=swap">
<style>
  :root {
    --backdrop: #222222;
    --ink: #000000;
    --paper: #ffffff;
    --steel: #8a8d8f;
    --soft-text: #d9d9d9;
  }
  * { box-sizing: border-box; margin: 0; padding: 0; }
  html, body {
    width: 1200px; height: 780px; overflow: hidden;
    background: var(--backdrop);
    font-family: "Open Sans", sans-serif;
  }
  .stage {
    position: relative; width: 1200px; height: 780px;
    display: flex; align-items: center; justify-content: center; gap: 60px;
  }
  .card {
    position: relative; width: 520px; height: 297px;
    overflow: hidden; background: var(--paper);
    box-shadow: 0 18px 40px rgba(0,0,0,.5);
  }
  .card-shapes { position: absolute; inset: 0; }

  /* Contact side */
  .holder { position: absolute; left: 36px; top: 116px; color: var(--paper); }
  .holder-name { font-weight: 700; font-size: 20px; letter-spacing: .5px; text-transform: uppercase; }
  .holder-role { font-size: 12px; color: var(--soft-text); margin-top: 2px; }
  .divider { position: absolute; left: 228px; top: 150px; width: 1px; height: 94px; background: var(--steel); }
  .contacts { position: absolute; left: 242px; top: 160px; list-style: none; color: var(--paper); font-size: 13px; line-height: 21px; }
  .contacts li { display: flex; align-items: center; gap: 7px; }
  .contacts svg { width: 11px; height: 11px; fill: var(--paper); flex: none; }
  .website {
    position: absolute; left: 0; right: 0; bottom: 0; height: 40px;
    padding-left: 36px; display: flex; align-items: center;
    color: var(--paper); font-size: 14px;
  }

  /* Brand mark */
  .brand { display: flex; align-items: center; gap: 10px; color: var(--ink); font-weight: 700; text-transform: uppercase; }
  .brand-square { background: var(--ink); flex: none; }
  .brand--small { position: absolute; left: 268px; top: 66px; font-size: 15px; }
  .brand--small .brand-square { width: 16px; height: 16px; }
  .brand--large { position: absolute; inset: 0; justify-content: center; font-size: 24px; gap: 14px; }
  .brand--large .brand-square { width: 26px; height: 26px; }
</style>
</head>
<body>
<main class="stage">

  <section class="card card--contact">
    <svg class="card-shapes" viewBox="0 0 520 297" aria-hidden="true">
      <rect width="520" height="297" fill="var(--ink)"/>
      <path d="M118,0 Q230,200 520,222 L520,0 Z" fill="var(--steel)"/>
      <path d="M136,0 Q240,186 520,206 L520,0 Z" fill="var(--paper)"/>
      <path d="M142,0 Q246,180 520,200 L520,0 Z" fill="var(--ink)"/>
      <path d="M150,0 Q252,172 520,192 L520,0 Z" fill="var(--paper)"/>
      <rect y="257" width="520" height="40" fill="var(--steel)"/>
    </svg>

    <div class="brand brand--small"><span class="brand-square"></span>Cedar Ridge Mechanical</div>

    <div class="holder">
      <p class="holder-name">Daniel Morris</p>
      <p class="holder-role">Managing Director</p>
    </div>
    <span class="divider"></span>
    <ul class="contacts">
      <li><svg viewBox="0 0 24 24"><path d="M6.6 10.8a15 15 0 0 0 6.6 6.6l2.2-2.2a1 1 0 0 1 1-.25 11 11 0 0 0 3.6.6 1 1 0 0 1 1 1V20a1 1 0 0 1-1 1A17 17 0 0 1 3 4a1 1 0 0 1 1-1h3.5a1 1 0 0 1 1 1 11 11 0 0 0 .6 3.6 1 1 0 0 1-.25 1z"/></svg>123 456 789</li>
      <li><svg viewBox="0 0 24 24"><path d="M6 3h10v5H6zM4 9h16a2 2 0 0 1 2 2v7h-4v3H6v-3H2v-7a2 2 0 0 1 2-2zm4 7v3h8v-3z"/></svg>123 456 789</li>
      <li><svg viewBox="0 0 24 24"><path d="M7 1h10a2 2 0 0 1 2 2v18a2 2 0 0 1-2 2H7a2 2 0 0 1-2-2V3a2 2 0 0 1 2-2zm0 3v14h10V4z"/></svg>123 456 789</li>
      <li><svg viewBox="0 0 24 24"><path d="M2 5h20v14H2zm2 2v.5l8 5 8-5V7l-8 5z"/></svg>info@cedarridgemech.com</li>
    </ul>
    <p class="website">www.cedarridgemech.com</p>
  </section>

  <section class="card card--brand">
    <div class="brand brand--large"><span class="brand-square"></span>Cedar Ridge Mechanical</div>
  </section>

</main>
</body>
</html>
```